Create a flyer for our party getaway to Ibiza.

'The Drifted Ibiza Getaway'

Friday 14th July - Monday 17th July

DJ Varro & DJ Mercer brings together a jam-packed weekend schedule full of the best urban parties in Ibiza.

What's included?

4 Nights Of Entertainment
6 Parties In Total
1 Boat Party
1 Pool Party
2 Superclub Parties
1 Indoor Water Party
Bottomless Drinks (Boat Party Only)
An unbelievable experience
1 unbeatable price.

All this for 140€ (you save 50€ when you book with us)

Tickets avaialble from Tixlane & Gobrino

Target Market(s)

holiday goers

Industry/Entity Type

party, events, club, hip hop

Requirements
Must have
• good vibes
Nice to have
• nice catchy looking title

```html
<!DOCTYPE html>
<html lang="en">
<head>
<meta charset="utf-8">
<title>The Drifted Ibiza Getaway</title>
<link href="https://fonts.googleapis.com/css2?family=Anton&family=Great+Vibes&family=Poppins:wght@400;500;600;700&display=swap" rel="stylesheet">
<style>
  :root {
    --page: #e4e4e4;
    --night: #0a0308;
    --magenta: #e5089a;
    --yellow: #f7dc0c;
    --olive: #6e6200;
    --blue: #0a7ce8;
    --white: #ffffff;
    --ticket-orange: #f26a1b;
  }
  * { box-sizing: border-box; margin: 0; padding: 0; }
  html, body { width: 1200px; height: 1200px; overflow: hidden; }
  body {
    background: var(--page);
    font-family: 'Poppins', sans-serif;
    color: var(--white);
    position: relative;
  }
  .flyer {
    position: absolute;
    left: 215px; top: 56px;
    width: 771px; height: 1090px;
    background: var(--night);
    overflow: hidden;
  }
  .flyer__backdrop {
    position: absolute; inset: 0;
    background:
      radial-gradient(ellipse 70% 30% at 50% 58%, rgba(210, 30, 140, 0.75), transparent 70%),
      radial-gradient(ellipse 45% 25% at 85% 68%, rgba(70, 90, 220, 0.55), transparent 70%),
      radial-gradient(ellipse 45% 25% at 15% 70%, rgba(90, 80, 210, 0.45), transparent 70%),
      linear-gradient(180deg, #050104 0%, #1a0514 35%, #6a1256 58%, #3a0a30 78%, #0b0309 100%);
  }
  .flyer__kicker {
    position: absolute; top: 54px; left: 0; right: 0;
    text-align: center;
    font-weight: 500; font-size: 44px; letter-spacing: 0.5px;
    color: var(--magenta);
    line-height: 1;
    z-index: 2;
  }
  .flyer__headline { position: absolute; left: 0; top: 0; width: 771px; height: 360px; z-index: 1; }
  .flyer__script {
    position: absolute; top: 340px; left: 0; right: 0;
    text-align: center;
    font-family: 'Great Vibes', cursive;
    font-size: 112px; line-height: 1;
    color: var(--white);
    z-index: 2;
  }
  .flyer__dates {
    position: absolute; left: 143px; top: 440px;
    width: 484px; height: 43px;
    background: var(--magenta); border-radius: 4px;
    display: flex; align-items: center; justify-content: center;
    font-size: 25px; font-weight: 400; white-space: nowrap;
    z-index: 3;
  }
  .flyer__dates b { font-weight: 700; }
  .flyer__djs-photo {
    position: absolute; left: 146px; top: 494px;
    width: 426px; height: 286px;
    background: radial-gradient(ellipse 60% 70% at 50% 60%, #f1ecf4 0%, #cbb7d2 45%, rgba(120, 60, 120, 0) 80%);
    border-radius: 40% 40% 0 0;
  }
  .flyer__lineup {
    position: absolute; left: 175px; top: 776px;
    width: 420px; height: 39px;
    background: var(--blue); border-radius: 3px;
    display: flex; align-items: center; justify-content: center;
    font-weight: 700; font-size: 27px; white-space: nowrap;
  }
  .flyer__lineup span { font-weight: 400; margin: 0 6px; }
  .flyer__intro {
    position: absolute; top: 822px; left: 0; right: 0;
    text-align: center; font-size: 18px; line-height: 22px;
  }
  .flyer__includes {
    position: absolute; list-style: none;
    font-size: 14px; font-weight: 600; white-space: nowrap;
  }
  .flyer__includes li { display: flex; align-items: center; gap: 9px; }
  .flyer__includes--left { left: 78px; top: 888px; }
  .flyer__includes--left li { height: 17.2px; }
  .flyer__includes--right { left: 409px; top: 887px; }
  .flyer__includes--right li { height: 22.2px; gap: 6px; }
  .tick { width: 11px; height: 11px; flex: none; }
  .flyer__price {
    position: absolute; left: 121px; top: 980px;
    width: 529px; height: 30px;
    border: 1.5px solid var(--white); border-radius: 4px;
    display: flex; align-items: center;
  }
  .flyer__price-tag {
    width: 168px; height: 30px;
    background: var(--magenta);
    clip-path: polygon(0 0, 100% 0, 94% 100%, 0 100%);
    display: flex; align-items: center; padding-left: 10px;
    font-weight: 700; font-size: 15px; white-space: nowrap;
    margin: -1.5px 0 0 -1.5px;
  }
  .flyer__price-note { flex: 1; text-align: center; font-size: 16.5px; white-space: nowrap; }
  .flyer__tickets {
    position: absolute; top: 1022px; left: 0; right: 0;
    display: flex; align-items: center; justify-content: center; gap: 14px;
    font-size: 12px; white-space: nowrap;
  }
  .vendor { font-weight: 700; font-size: 19px; display: flex; align-items: center; gap: 6px; }
  .vendor__mark { width: 12px; height: 12px; background: var(--ticket-orange); }
</style>
</head>
<body>
  <main class="flyer">
    <div class="flyer__backdrop" role="img" aria-label="Photo of a club crowd under pink and blue stage lights"></div>

    <p class="flyer__kicker">THE DRIFTED</p>

    <svg class="flyer__headline" viewBox="0 0 771 360" aria-label="Ibiza">
      <defs>
        <linearGradient id="ibiza-fill" x1="0" y1="110" x2="0" y2="350" gradientUnits="userSpaceOnUse">
          <stop offset="0" stop-color="#f9df0b"/>
          <stop offset="0.35" stop-color="#f0d40a"/>
          <stop offset="1" stop-color="#6e6200"/>
        </linearGradient>
      </defs>
      <text x="137" y="352" font-family="Anton, sans-serif" font-size="278" textLength="520" lengthAdjust="spacingAndGlyphs" fill="#000" stroke="var(--yellow)" stroke-width="3">IBIZA</text>
      <text x="129" y="349" font-family="Anton, sans-serif" font-size="278" textLength="518" lengthAdjust="spacingAndGlyphs" fill="url(#ibiza-fill)">IBIZA</text>
    </svg>

    <p class="flyer__script">Getaway</p>

    <div class="flyer__dates">Friday&nbsp;<b>14th July</b>&nbsp;<b>-</b>&nbsp;Monday&nbsp;<b>17th July</b></div>

    <div class="flyer__djs-photo" role="img" aria-label="Photo of the two DJs posing together in white t-shirts"></div>

    <div class="flyer__lineup">DJ VARRO<span>&amp;</span>DJ MERCER</div>

    <p class="flyer__intro">brings together a jam-packed weekend schedule full of the<br>best urban parties in Ibiza</p>

    <ul class="flyer__includes flyer__includes--left">
      <li><svg class="tick" viewBox="0 0 12 12"><circle cx="6" cy="6" r="6" fill="var(--magenta)"/><path d="M3.2 6.2l1.9 1.8 3.7-3.8" stroke="#fff" stroke-width="1.4" fill="none"/></svg>4 Nights Of Entertainment</li>
      <li><svg class="tick" viewBox="0 0 12 12"><circle cx="6" cy="6" r="6" fill="var(--magenta)"/><path d="M3.2 6.2l1.9 1.8 3.7-3.8" stroke="#fff" stroke-width="1.4" fill="none"/></svg>6 Parties In Total</li>
      <li><svg class="tick" viewBox="0 0 12 12"><circle cx="6" cy="6" r="6" fill="var(--magenta)"/><path d="M3.2 6.2l1.9 1.8 3.7-3.8" stroke="#fff" stroke-width="1.4" fill="none"/></svg>1 Boat Party</li>
      <li><svg class="tick" viewBox="0 0 12 12"><circle cx="6" cy="6" r="6" fill="var(--magenta)"/><path d="M3.2 6.2l1.9 1.8 3.7-3.8" stroke="#fff" stroke-width="1.4" fill="none"/></svg>1 Pool Party</li>
      <li><svg class="tick" viewBox="0 0 12 12"><circle cx="6" cy="6" r="6" fill="var(--magenta)"/><path d="M3.2 6.2l1.9 1.8 3.7-3.8" stroke="#fff" stroke-width="1.4" fill="none"/></svg>2 Superclub Parties</li>
    </ul>

    <ul class="flyer__includes flyer__includes--right">
      <li><svg class="tick" viewBox="0 0 12 12"><circle cx="6" cy="6" r="6" fill="var(--magenta)"/><path d="M3.2 6.2l1.9 1.8 3.7-3.8" stroke="#fff" stroke-width="1.4" fill="none"/></svg>1 Indoor Water Party</li>
      <li><svg class="tick" viewBox="0 0 12 12"><circle cx="6" cy="6" r="6" fill="var(--magenta)"/><path d="M3.2 6.2l1.9 1.8 3.7-3.8" stroke="#fff" stroke-width="1.4" fill="none"/></svg>Bottomless Drinks (Boat Party Only)</li>
      <li><svg class="tick" viewBox="0 0 12 12"><circle cx="6" cy="6" r="6" fill="var(--magenta)"/><path d="M3.2 6.2l1.9 1.8 3.7-3.8" stroke="#fff" stroke-width="1.4" fill="none"/></svg>An unbelievable experience</li>
      <li><svg class="tick" viewBox="0 0 12 12"><circle cx="6" cy="6" r="6" fill="var(--magenta)"/><path d="M3.2 6.2l1.9 1.8 3.7-3.8" stroke="#fff" stroke-width="1.4" fill="none"/></svg>1 unbeatable price</li>
    </ul>

    <div class="flyer__price">
      <div class="flyer__price-tag">ALL THIS FOR 140€</div>
      <div class="flyer__price-note">(you save 50€ when you book with us)</div>
    </div>

    <div class="flyer__tickets">
      <span>Tickets avaialble from Tixlane &amp; Gobrino</span>
      <span class="vendor">Gobrino</span>
      <span class="vendor"><span class="vendor__mark"></span>Tixlane</span>
    </div>
  </main>
</body>
</html>
```